Menu Design Project

Menu design for a Japanese fast food restaurant featuring Teppanyaki and Sushi. The restaurant main scene color is black and wood color. No Japan scenery pictures. Menu try to be simply and elegant . Pictures provided can be used accordingly to the menu items, but doesn't have to be due to the back ground color of the picture is white.

Target Market(s)

Young and progressive consumers

Industry/Entity Type

Asian Restaurant

Font styles to use
Other font styles liked:
• Han Wang Kan Tan Font

Colors
1b1b1b
fee18a

Requirements
Must have
• Pictures of the Sushi that is provided, and all the item in the Word file.
Nice to have
• Keep it simple but different
Should not have
• No scenery pictures, no cherry blossom.

```html
<!DOCTYPE html>
<html lang="en">
<head>
<meta charset="utf-8">
<title>Sushi Menu</title>
<link href="https://fonts.googleapis.com/css2?family=Oswald:wght@600;700&family=Source+Sans+3:wght@400;600&display=swap" rel="stylesheet">
<style>
:root{
  --ink:#1b1b1b;
  --butter:#fee18a;
  --paper:#ffffff;
  --cream:#f4f1e8;
  --warn:#f5c84a;
  --panel-grey:#3a3a3a;
}
*{margin:0;padding:0;box-sizing:border-box}
html,body{width:1200px;height:928px;overflow:hidden;background:var(--butter)}
.menu{position:relative;width:1200px;height:928px;overflow:hidden;font-family:"Source Sans 3",Arial,sans-serif;color:var(--paper)}
.backdrop{position:absolute;inset:0}
.abs{position:absolute}
.band{position:absolute;background:var(--butter);color:var(--ink);font-family:"Oswald","Arial Narrow",sans-serif;font-weight:700;text-align:center;letter-spacing:.5px}
.band.left{left:0;width:403px;font-size:33px;line-height:44px;height:44px}
.name{font-size:15.5px;font-weight:600;text-transform:uppercase;line-height:18px}
.name small{font-size:13px;text-transform:none;font-weight:400}
.desc{font-size:13px;line-height:16px;color:#e8e8e8}
.price{position:absolute;font-size:13.5px;font-weight:600;text-align:right}
.appetizer .item,.specials .item,.rolls .item,.maki .item{position:absolute}
.photo{position:absolute;border-radius:6px}
.thumbs{position:absolute;left:403px;top:74px;width:74px;height:652px;background:var(--paper)}
.thumb{position:absolute;left:8px;width:58px;height:34px;border-radius:4px;background:linear-gradient(135deg,#9cc46b,#e88a5a)}
.sizes{position:absolute;font-size:12.5px;font-weight:600;line-height:16px;white-space:nowrap}
.sizes span{font-size:11px}
.caution{position:absolute;left:805px;top:583px;width:395px;height:60px;background:var(--panel-grey);text-align:center;padding-top:10px}
.caution b{display:block;color:var(--warn);font-size:14.5px;font-weight:600;line-height:15px}
.caution p{color:var(--warn);font-size:11.5px;line-height:12px}
.hand .label{font-size:15.5px;font-weight:600;line-height:17px}
.hand .desc{margin-bottom:4px}
</style>
</head>
<body>
<div class="menu">
  <svg class="backdrop" width="1200" height="928" viewBox="0 0 1200 928" aria-hidden="true">
    <rect width="1200" height="928" fill="var(--butter)"/>
    <polygon points="0,45 400,38 400,842 0,842" fill="var(--ink)"/>
    <polygon points="0,842 400,842 400,880 0,905" fill="var(--ink)"/>
    <polygon points="403,30 805,30 805,918 403,925" fill="var(--ink)"/>
    <polygon points="805,130 1200,115 1200,660 1000,928 805,928" fill="var(--ink)"/>
    <polygon points="805,20 940,0 1200,0 1200,115 805,130" fill="var(--butter)"/>
  </svg>

  <!-- LEFT COLUMN -->
  <div class="band left" style="top:53px">APPETIZER</div>
  <div class="appetizer">
    <div class="item abs" style="left:27px;top:102px"><div class="name">Seaweed Salad</div><div class="desc">seasoned seaweed</div></div>
    <div class="price" style="right:812px;top:119px">$2.99</div>
    <div class="item abs" style="left:27px;top:138px"><div class="name">Kani Salad Spicy or Non-Spicy</div><div class="desc">crab meat, cucumber, lettuce with dressing</div></div>
    <div class="price" style="right:812px;top:154px">$3.99</div>
    <div class="item abs" style="left:27px;top:193px"><div class="name">Tempura Shrimp</div><div class="desc">4 Pieces Fried Tempura Shrimp</div></div>
    <div class="price" style="right:812px;top:209px">$5.99</div>
    <div class="photo" role="img" aria-label="Fried tempura shrimp" style="left:240px;top:178px;width:90px;height:80px;background:radial-gradient(circle,#f6d24a,#e0a820 70%,transparent 72%)"></div>
    <div class="item abs" style="left:27px;top:269px"><div class="name">Fried Gyoza <small>(6pcs)</small></div></div>
    <div class="price" style="right:812px;top:270px">$3.99</div>
    <div class="item abs" style="left:27px;top:289px"><div class="name">Spring Roll <small>(4pcs)</small></div></div>
    <div class="price" style="right:812px;top:290px">$2.59</div>
    <div class="item abs" style="left:27px;top:310px"><div class="name">Crab Rangoon <small>(5pcs)</small></div></div>
    <div class="price" style="right:812px;top:311px">$4.50</div>
  </div>

  <div class="band left" style="top:340px">SASHIMI</div>
  <div class="desc abs" style="left:27px;top:399px;width:180px">*Salmon, *Tuna, *Yellow Tail, *Red Snapper, *White Tuna, Surf Clam</div>
  <div class="photo" role="img" aria-label="Sashimi slices" style="left:207px;top:395px;width:195px;height:50px;background:linear-gradient(90deg,#f5a27a,#e0445a,#f7c2a8,#f3e0b8)"></div>

  <div class="band left" style="top:462px">SUSHI NIGIRI</div>
  <div class="desc abs" style="left:27px;top:515px;width:200px">*Salmon, *Tuna, *Yellow Tail, *Red Snapper, *White Tuna, Surf Clam, Grill Eel, Ebi Shrimp, Kani crab meat</div>
  <div class="photo" role="img" aria-label="Salmon nigiri" style="left:262px;top:508px;width:108px;height:52px;border-radius:50%;background:linear-gradient(160deg,#f8a060,#fbe2cf)"></div>
  <div class="desc abs" style="left:264px;top:561px;color:#fff">5 pieces for <b style="font-size:14px">$5.99</b></div>

  <div class="band left" style="top:590px;height:68px;font-size:33px;line-height:33px">HAND ROLL BUILD YOUR<br>OWN:</div>
  <div class="hand abs" style="left:27px;top:669px;width:270px">
    <div class="label">PICK ONE PROTEIN:</div>
    <div class="desc">*Salmon, *Tuna, *Yellow Tail, *Red Snapper, *White Tuna, Surf Clam, Grill Eel, Ebi Shrimp, Kani crab meat</div>
    <div class="label">PICK TWO VEGETABLE:</div>
    <div class="desc">Cucumber, Avocado, Lettuce, Oshigo, Asparagus, Seaweed</div>
    <div class="label">PICK SAUCE:</div>
    <div class="desc">Spicy Mayonnaise, Honey Wasabi, Honey Mayonnaise, Unagi Sauce</div>
  </div>
  <div class="photo" role="img" aria-label="Hand roll cone" style="left:308px;top:672px;width:60px;height:135px;background:linear-gradient(180deg,#6e8f3a,#2a3a2a 40%,#1f2a22)"></div>
  <div class="desc abs" style="left:318px;top:812px;color:#fff">2 for<b style="font-size:14px">$5.99</b></div>

  <!-- CENTER COLUMN -->
  <div class="band" style="left:403px;top:30px;width:402px;height:44px;font-size:35px;line-height:44px">SUSHI</div>
  <div class="thumbs" role="img" aria-label="Roll photos">
    <div class="thumb" style="top:55px"></div>
    <div class="thumb" style="top:160px"></div>
    <div class="thumb" style="top:210px"></div>
    <div class="thumb" style="top:305px"></div>
    <div class="thumb" style="top:355px"></div>
    <div class="thumb" style="top:405px"></div>
    <div class="thumb" style="top:460px"></div>
    <div class="thumb" style="top:510px;width:34px;left:20px;border-radius:50%"></div>
  </div>
  <div class="abs" style="left:503px;top:83px;font-size:15px">Ingredients subject to availability</div>
  <div class="abs" style="left:485px;top:100px;font-size:22px;font-weight:600;line-height:24px">SPECIAL ROLL</div>
  <div class="specials">
    <div class="item" style="left:485px;top:126px"><div class="name">Dragon Roll</div><div class="desc">Grilled Eel fish &amp; cucumber top with<br>avocado &amp; Unagi sauce</div></div><div class="price" style="right:408px;top:161px">$9.99</div>
    <div class="item" style="left:485px;top:179px"><div class="name">Deluxe Black Dragon Roll</div><div class="desc">Tempura Shrimp top with Avocado,<br>Grilled Eel fish &amp; Unagi sacue</div></div><div class="price" style="right:402px;top:214px">$11.99</div>
    <div class="item" style="left:485px;top:232px"><div class="name">*Rainbow Roll</div><div class="desc">avocado, cucumber &amp; Kani top with red<br>snapper, tuna, salmon&amp;avocado</div></div><div class="price" style="right:402px;top:267px">$10.99</div>
    <div class="item" style="left:485px;top:285px"><div class="name">*Four Season Roll</div><div class="desc">Tuna, salmon, oshinko</div></div><div class="price" style="right:408px;top:303px">$9.99</div>
    <div class="item" style="left:485px;top:321px"><div class="name">*Deluxe Philly Roll</div><div class="desc">Salmon, cream cheese &amp; avocado top<br>with more salmon</div></div><div class="price" style="right:420px;top:355px">$9.9</div>
    <div class="item" style="left:485px;top:374px"><div class="name">*Massago Roll</div><div class="desc">Kani crab meat, cucumber &amp; avocado top<br>with Premium Massago Roe</div></div><div class="price" style="right:408px;top:408px">$8.99</div>
    <div class="item" style="left:485px;top:427px"><div class="name">*Deluxe Spicy Tuna Roll</div><div class="desc">Kani crab meat, Cucumber &amp; avocado top<br>with Spicy grounded tuna</div></div><div class="price" style="right:408px;top:461px">$9.49</div>
    <div class="item" style="left:485px;top:480px"><div class="name">Deluxe Spicy Kani Roll</div><div class="desc">Kani crab meat, cucumber &amp; avocado top<br>with seasoned ground Crab meat</div></div><div class="price" style="right:408px;top:514px">$9.49</div>
    <div class="item" style="left:485px;top:532px"><div class="name">Deluxe Kani Roll</div><div class="desc">Kani crab meat, cucumber &amp; avocado top<br>with Kani &amp; Panko crumb</div></div><div class="price" style="right:408px;top:566px">$9.49</div>
    <div class="item" style="left:485px;top:585px"><div class="name">*Tri Deluxe Fish Roll</div><div class="desc">Tuna, salmon &amp; red snapper</div></div><div class="price" style="right:408px;top:603px">$9.99</div>
    <div class="item" style="left:485px;top:621px"><div class="name">*Sumo Roll</div><div class="desc">Tuna, Salmon, White Tuan, Red snapper<br>Avocado &amp; Kani Crab Meat</div></div><div class="price" style="right:402px;top:655px">$10.99</div>
    <div class="item" style="left:485px;top:674px"><div class="name">*Hamachi Asparagus Roll</div><div class="desc">Hamachi, Scallion &amp; Asparagus with Ponzu<br>Sauce</div></div><div class="price" style="right:408px;top:708px">$7.99</div>
  </div>

  <div class="band" style="left:403px;top:726px;width:402px;height:44px;font-size:33px;line-height:44px">REGULAR MAKI ROLL</div>
  <div class="maki">
    <div class="item" style="left:420px;top:781px"><div class="name">*Salmon Roll</div><div class="desc" style="margin-top:3px">salmon &amp; avocado</div></div>
    <div class="sizes" style="left:692px;top:783px"><span>(8pcs)</span> $5.49<br><span>(12pcs)</span> $7.49</div>
    <div class="item" style="left:420px;top:820px"><div class="name">*Tuna Roll</div><div class="desc" style="margin-top:3px">tuna &amp; avocado</div></div>
    <div class="sizes" style="left:692px;top:822px"><span>(8pcs)</span> $5.49<br><span>(12pcs)</span> $7.49</div>
    <div class="item" style="left:420px;top:859px"><div class="name">*Philly Roll</div><div class="desc" style="margin-top:3px">salmon, cream cheese &amp; avocado</div></div>
    <div class="sizes" style="left:692px;top:861px"><span>(8pcs)</span> $5.49<br><span>(12pcs)</span> $7.49</div>
  </div>

  <!-- RIGHT COLUMN -->
  <div class="photo" role="img" aria-label="Tuna, snapper and salmon nigiri" style="left:825px;top:42px;width:355px;height:90px;border-radius:45px;background:linear-gradient(90deg,#e0303f,#f4a8a0 45%,#f6c3b4 55%,#f58a55)"></div>
  <div class="rolls">
    <div class="item" style="left:811px;top:158px"><div class="name">California Roll</div><div class="desc" style="margin-top:3px">cucumber, avocado &amp; kani crab meat</div></div>
    <div class="sizes" style="left:1084px;top:160px"><span>(8pcs)</span> $5.49<br><span>(12pcs)</span> $7.49</div>
    <div class="item" style="left:811px;top:200px"><div class="name">Kani &amp; Cheese Roll</div><div class="desc">Kani crab meat &amp; cream cheese</div></div>
    <div class="sizes" style="left:1084px;top:202px"><span>(8pcs)</span> $5.49<br><span>(12pcs)</span> $7.49</div>
    <div class="item" style="left:811px;top:246px"><div class="name">Shrimp Tempura Roll</div><div class="desc">Fried tempura shrimp &amp; cucumber</div></div>
    <div class="sizes" style="left:1084px;top:264px"><span>(8pcs)</span> $6.49</div>
    <div class="item" style="left:811px;top:292px"><div class="name">*Alaska Roll</div><div class="desc">Salmon &amp; avocado with massago</div></div>
    <div class="photo" role="img" aria-label="Alaska roll pieces" style="left:1016px;top:277px;width:54px;height:52px;background:linear-gradient(180deg,#f08a3a,#f4f1e8)"></div>
    <div class="sizes" style="left:1084px;top:294px"><span>(8pcs)</span> $5.49<br><span>(12pcs)</span> $7.49</div>
    <div class="item" style="left:811px;top:337px"><div class="name">Grilled Eel Roll</div><div class="desc">Eel &amp; avocado</div></div>
    <div class="sizes" style="left:1084px;top:339px"><span>(8pcs)</span> $5.49<br><span>(12pcs)</span> $7.49</div>
    <div class="item" style="left:811px;top:382px"><div class="name">*Spicy Tuna Roll</div><div class="desc">seasoned ground tuna</div></div>
    <div class="sizes" style="left:1084px;top:384px"><span>(8pcs)</span> $5.49<br><span>(12pcs)</span> $7.49</div>
    <div class="item" style="left:811px;top:427px"><div class="name">*Spicy Salmon Roll</div><div class="desc">seasoned ground salmon</div></div>
    <div class="sizes" style="left:1084px;top:429px"><span>(8pcs)</span> $5.49<br><span>(12pcs)</span> $7.49</div>
    <div class="item" style="left:811px;top:472px"><div class="name">Spicy Kani Roll</div><div class="desc">seasoned ground crab meat</div></div>
    <div class="sizes" style="left:1084px;top:474px"><span>(8pcs)</span> $5.49<br><span>(12pcs)</span> $7.49</div>
    <div class="item" style="left:811px;top:518px"><div class="name">Vegetarian Roll</div><div class="desc">avocado, cucumber<br>Add Ajitsuke seasoned fried bean curd</div></div>
    <div class="sizes" style="left:1084px;top:520px"><span>(8pcs)</span> $4.49<br><span>(16pcs)</span> $7.99<br>for $1.00 more</div>
  </div>

  <div class="caution">
    <b>*ITEMS MAY BE SERVED RAW OR UNDER COOKED</b>
    <p>consuming raw or undercooked meat, poultry, shellfish, eggs<br>or seafood may increase your risk of food borne illness.</p>
  </div>

  <div class="photo" role="img" aria-label="Close-up of a salmon avocado maki roll" style="left:900px;top:660px;width:250px;height:240px;border-radius:40px;background:radial-gradient(circle at 50% 50%,#f49a6a 0,#f1efe6 35%,#e4e0d4 70%,#d8d3c4)"></div>
</div>
</body>
</html>
```